Business Card Design For Office Furniture Clearance Company

Kestrel Office Clearance - our company name pretty much explains what we do, we clear offices for high end clients, mainly plc's and large international companies.

We require a nice looking business card that displays professionalism but without being too serious.

It would be nice to see just a little more than a conventional boring business card, make sure you add some flare.

Industry/Entity Type

Office Furniture

Contact Information for Business Card

CARD 1

Mark Holloway
Director
mark@kestrelofficeclearance.co.uk
m: 07700 153928

t: 01632 960418
www.kestrelofficeclearance.co.uk

Kestrel Office Clearance
Unit K4 B
2-8 Fenwick Lane
Harwick
Dunmere Vale
ZZ9 4QT

free office clearances… you cant get better than that.

CARD 2

Peter Radford
Director
peter@kestrelofficeclearance.co.uk
m: 07700 382615

t: 01632 960418

Kestrel Office Clearance
Unit K4 B
2-8 Fenwick Lane
Harwick
Dunmere Vale
ZZ9 4QT

Font styles to use
Sans Serif

Requirements
Must have
• A white background - as we have a blue logo.
Nice to have
• Nice use of the logo - play around with this and dissect it.

```html
<!DOCTYPE html>
<html lang="en">
<head>
<meta charset="utf-8">
<title>Kestrel Office Clearance – Business Card</title>
<link href="https://fonts.googleapis.com/css2?family=Lato:wght@400;700;900&display=swap" rel="stylesheet">
<style>
  :root {
    --brand-blue: #0a7abf;
    --brand-blue-deep: #08609a;
    --paper: #ffffff;
    --ink: #333a40;
    --backdrop: #767474;
  }
  * { box-sizing: border-box; margin: 0; padding: 0; }
  html, body { width: 1200px; height: 900px; overflow: hidden; }
  body {
    background: var(--backdrop);
    font-family: "Lato", Arial, sans-serif;
    position: relative;
  }
  .card {
    position: absolute;
    width: 520px;
    height: 300px;
    border-radius: 14px;
    overflow: hidden;
    box-shadow: 0 6px 18px rgba(0,0,0,.25);
  }
  /* Back side */
  .card-back {
    left: 70px; top: 110px;
    background: var(--brand-blue);
  }
  .card-back .brand-lockup {
    position: absolute;
    left: 0; right: 0; top: 110px;
    display: flex; align-items: center; justify-content: center; gap: 14px;
  }
  .card-back .brand-dot {
    width: 46px; height: 46px; border-radius: 50%;
    background: var(--brand-blue-deep);
  }
  .card-back .brand-name {
    color: var(--paper);
    font-weight: 900;
    font-size: 26px;
  }
  .card-back .back-url {
    position: absolute;
    left: 0; right: 0; bottom: 26px;
    text-align: center;
    color: var(--paper);
    font-size: 12px;
  }
  /* Front side */
  .card-front {
    left: 610px; top: 490px;
    background: var(--paper);
  }
  .company-title {
    position: absolute;
    left: 26px; top: 52px;
    color: var(--brand-blue);
    font-weight: 900;
    font-size: 30px;
    letter-spacing: -0.3px;
    white-space: nowrap;
  }
  .info-band {
    position: absolute;
    left: 0; right: 0; top: 128px; height: 128px;
    background: var(--brand-blue);
  }
  .brand-circle {
    position: absolute;
    left: 372px; top: 66px;
    width: 128px; height: 128px;
    border-radius: 50%;
    background: var(--brand-blue);
    border: 4px solid var(--paper);
    box-shadow: 0 0 0 3px var(--brand-blue);
  }
  .contact {
    position: absolute;
    left: 40px; top: 140px;
    color: var(--paper);
  }
  .contact .person-name { font-weight: 700; font-size: 20px; line-height: 1.1; }
  .contact .person-role { font-size: 12px; margin-bottom: 8px; }
  .contact-list { list-style: none; }
  .contact-list li {
    display: flex; align-items: center; gap: 8px;
    font-size: 12px; line-height: 16px;
    white-space: nowrap;
  }
  .contact-list svg { width: 12px; height: 12px; flex: none; }
  .address {
    position: absolute;
    left: 40px; bottom: 16px;
    color: var(--ink);
    font-size: 12px;
    white-space: nowrap;
  }
</style>
</head>
<body>

<section class="card card-back">
  <div class="brand-lockup">
    <span class="brand-dot"></span>
    <span class="brand-name">Kestrel Office Clearance</span>
  </div>
  <p class="back-url">www.kestrelofficeclearance.co.uk</p>
</section>

<section class="card card-front">
  <h1 class="company-title">Kestrel Office Clearance</h1>
  <div class="info-band"></div>
  <div class="brand-circle"></div>
  <div class="contact">
    <p class="person-name">Mark Holloway</p>
    <p class="person-role">Director</p>
    <ul class="contact-list">
      <li>
        <svg viewBox="0 0 12 12"><rect x="3" y="0.8" width="6" height="10.4" rx="1" fill="none" stroke="#fff" stroke-width="1.2"/><circle cx="6" cy="9.3" r="0.6" fill="#fff"/></svg>
        07700 153928
      </li>
      <li>
        <svg viewBox="0 0 12 12"><path d="M2.5 1.5 L4.5 1 L5.5 3.8 L4.2 4.8 Q5 7 7.2 7.8 L8.2 6.5 L11 7.5 L10.5 9.5 Q9.5 11 7.5 10.4 Q2.2 8.5 1.2 3.8 Q1 2.2 2.5 1.5 Z" fill="#fff"/></svg>
        01632 960418
      </li>
      <li>
        <svg viewBox="0 0 12 12"><rect x="0.8" y="2.5" width="10.4" height="7" fill="none" stroke="#fff" stroke-width="1.1"/><path d="M0.8 2.5 L6 6.5 L11.2 2.5" fill="none" stroke="#fff" stroke-width="1.1"/></svg>
        mark@kestrelofficeclearance.co.uk
      </li>
      <li>
        <svg viewBox="0 0 12 12"><circle cx="6" cy="6" r="5" fill="none" stroke="#fff" stroke-width="1"/><ellipse cx="6" cy="6" rx="2.2" ry="5" fill="none" stroke="#fff" stroke-width="0.9"/><path d="M1 6 H11 M2 3.4 H10 M2 8.6 H10" stroke="#fff" stroke-width="0.8"/></svg>
        www.kestrelofficeclearance.co.uk
      </li>
    </ul>
  </div>
  <p class="address">Unit K4 B 2-8 Fenwick Lane, Harwick Dunmere Vale, ZZ9 4QT</p>
</section>

</body>
</html>
```